Bookcover: Ways to Turn Into a Bold Pathfinder

I am publishing a super-low-cost innovation book for €4,99 on Quillmere Open Press to help everyone become a great innovator: young ambitious people without college education nor a big budget. Do you want to help me?

Brief:
Design a book cover 1600 x 2560 pixels for QOP.
Main title: Ways to Turn Into a Bold Pathfinder
Sub title: mindset - insights - skills & tools
Author: Joost ter Brakel
Design: captive, and appealing to everyone
Target Group: young ambitious people without college education

For quillmere please format the height/width ratio of 1.6:1

```html
<!DOCTYPE html>
<html lang="en">
<head>
<meta charset="utf-8">
<title>Ways to Turn Into a Bold Pathfinder — Book Cover</title>
<link rel="stylesheet" href="https://fonts.googleapis.com/css2?family=Bebas+Neue&family=Montserrat:wght@800&display=swap">
<style>
  :root {
    --backdrop: #8f8f8f;
    --paper: #faf9f9;
    --ink: #231f20;
    --accent-red: #e31826;
    --accent-blue: #6096e6;
    --shadow-grey: #b8b8b8;
  }
  html, body {
    margin: 0;
    width: 1200px;
    height: 1200px;
    overflow: hidden;
    background: var(--backdrop);
  }
  .book-cover {
    position: absolute;
    left: 293px;
    top: 140px;
    width: 614px;
    height: 919px;
    background: var(--paper);
  }
  .book-cover svg { display: block; width: 100%; height: 100%; }
  .title-display { font-family: "Bebas Neue", "Oswald", sans-serif; }
  .title-kicker { fill: var(--ink); font-size: 63px; }
  .title-line-dark { fill: var(--ink); font-size: 178px; }
  .title-line-red { fill: var(--accent-red); font-size: 248px; }
  .title-line-blue { fill: var(--accent-blue); font-size: 163px; }
  .rule { stroke: var(--ink); stroke-width: 2; }
  .subtitle, .author {
    font-family: "Montserrat", "Arial", sans-serif;
    font-weight: 800;
    fill: var(--ink);
  }
  .subtitle { font-size: 30px; }
  .author { font-size: 24px; }
</style>
</head>
<body>
  <main class="book-cover">
    <svg viewBox="0 0 614 919" xmlns="http://www.w3.org/2000/svg">
      <defs>
        <linearGradient id="artwork-tones" x1="0" y1="0" x2="1" y2="1">
          <stop offset="0" stop-color="#f6b21a"/>
          <stop offset="0.35" stop-color="#ee6a22"/>
          <stop offset="0.6" stop-color="#c8362f"/>
          <stop offset="0.8" stop-color="#2a6fb6"/>
          <stop offset="1" stop-color="#2a3440"/>
        </linearGradient>
        <radialGradient id="ground-shadow" cx="0.5" cy="0.5" r="0.5">
          <stop offset="0" stop-color="var(--shadow-grey)"/>
          <stop offset="1" stop-color="var(--paper)" stop-opacity="0"/>
        </radialGradient>
      </defs>

      <g class="title-block">
        <line class="rule" x1="41" y1="61" x2="222" y2="61"/>
        <line class="rule" x1="391" y1="61" x2="571" y2="61"/>
        <text class="title-display title-kicker" x="236" y="84" textLength="142" lengthAdjust="spacingAndGlyphs">WAYS TO</text>
        <text class="title-display title-line-dark" x="41" y="222" textLength="530" lengthAdjust="spacingAndGlyphs">TURN INTO A</text>
        <text class="title-display title-line-red" x="81" y="407" textLength="448" lengthAdjust="spacingAndGlyphs">BOLD</text>
        <text class="title-display title-line-blue" x="41" y="530" textLength="530" lengthAdjust="spacingAndGlyphs">PATHFINDER</text>
      </g>

      <text class="subtitle" x="41" y="575" textLength="530" lengthAdjust="spacingAndGlyphs">MINDSET - INSIGHTS - SKILLS &amp; TOOLS</text>

      <g class="cover-artwork">
        <ellipse cx="306" cy="865" rx="92" ry="6" fill="url(#ground-shadow)"/>
        <rect role="img" aria-label="Colourful illustration of a light bulb merged with a head silhouette, filled with gears and sketches" x="215" y="597" width="219" height="256" rx="100" fill="url(#artwork-tones)"/>
      </g>

      <text class="author" x="206" y="906" textLength="203" lengthAdjust="spacingAndGlyphs">JOOST TER BRAKEL</text>
    </svg>
  </main>
</body>
</html>
```